zorvan lumet website design

An IT support and IT Security Company - just use dummy text for now for the design. Examples of sites we like the looks and feel of but need it more professional feel are like: www.kelbrovault.uk.com , www.pravok.co.uk, www.quenthardy.com/professional/, www.vur.com, www.melvish.com,

Best to message me if you have any questions

Target Market(s)

small to medium UK based companies that require IT support services

Industry/Entity Type

It Company

Contact Information for Business Card

use dummy name, telephone and email for now, will provide details later.

Logo Text

zorvan lumet (and then below the logo it should say "your IT, networks and security partner")

Coding

Coded - Design and coding required

Number of Pages Required

5+ page

Colors

Designer to choose colors to be used in the design.

Requirements
Must have
• must be professional, yet simple and clear that this is a serious IT support and IT security company.
Nice to have
• 1)The website homepage must have professional quality pictures of IT support or London city skyline or any picture that projects friendly business partners, professionalism and ready to serve.
• 2) Home page needs to include tabs for following pages 'Services' , 'About Us' , 'Contact Us' 'Home'
• 3) Website built customised using wordpress is ideal and easy for us to manage.
• more room for boxed options from homepage (with pic or image in background)
Should not have
• no checkout trolleys or payment options.

```html
<!DOCTYPE html>
<html lang="en">
<head>
<meta charset="utf-8">
<title>zorvan lumet – IT support and IT security</title>
<link rel="stylesheet" href="https://fonts.googleapis.com/css2?family=Asap:ital,wght@0,400;0,500;0,700;1,400&family=Bree+Serif&family=Raleway:wght@700&display=swap">
<style>
  :root {
    --brand: #26a6cf;
    --brand-dark: #1e93b9;
    --ink: #4a4a4a;
    --body: #6a6a6a;
    --muted: #8c8c8c;
    --paper: #ffffff;
    --band: #eeeeee;
    --footer: #333333;
    --footer-deep: #2d2d2d;
    --footer-line: #4a4a4a;
    --footer-text: #e6e6e6;
  }
  * { box-sizing: border-box; margin: 0; padding: 0; }
  html, body { width: 1200px; height: 3077px; overflow: hidden; }
  body {
    position: relative;
    background: var(--paper);
    font-family: "Asap", Arial, sans-serif;
    color: var(--body);
  }
  section, header, footer { position: absolute; left: 0; width: 1200px; }
  .abs { position: absolute; }

  /* Hero */
  .hero { top: 0; height: 626px; overflow: hidden; }
  .hero-art {
    position: absolute; inset: 0;
    background:
      radial-gradient(ellipse 520px 360px at 720px 330px, rgba(170,205,225,.85), rgba(170,205,225,0) 70%),
      radial-gradient(ellipse 420px 300px at 250px 260px, rgba(200,228,240,.9), rgba(200,228,240,0) 70%),
      linear-gradient(120deg, #e4f2f8 0%, #d3e6ef 45%, #dfe9ef 70%, #eef3f6 100%);
  }
  .main-nav {
    position: absolute; top: 34px; left: 0; width: 1200px;
    display: flex; justify-content: center; gap: 38px;
    font-size: 16px; letter-spacing: .3px; text-transform: uppercase;
  }
  .main-nav a { color: #3f4a52; text-decoration: none; }
  .main-nav a.active { color: var(--brand); }
  .hero-title {
    position: absolute; top: 250px; left: 0; width: 1200px; text-align: center;
    font-family: "Raleway", "Asap", sans-serif; font-weight: 700;
    font-size: 112px; line-height: 1; color: var(--brand); letter-spacing: -1px;
  }

  /* Headings */
  .section-title {
    font-family: "Bree Serif", Georgia, serif; font-weight: 400;
    color: var(--brand); font-size: 40px; line-height: 1;
    text-align: center; position: absolute; left: 0; width: 1200px;
  }
  p { font-size: 14.5px; line-height: 25px; }

  /* About */
  .about { top: 626px; height: 512px; }
  .about-frame {
    left: 78px; top: 96px; width: 519px; height: 324px;
    border: 2px solid #e2e2e2; border-radius: 26px; background: var(--paper);
    box-shadow: 0 4px 14px rgba(0,0,0,.08);
  }
  .about-photo {
    left: 53px; top: 10px; width: 417px; height: 302px; border-radius: 6px;
    background: linear-gradient(135deg, #c9ccd0 0%, #e4e7ea 40%, #9aa4ad 70%, #d6d9dc 100%);
  }
  .about-copy { left: 669px; top: 152px; width: 452px; }
  .about-copy h2 {
    font-family: "Bree Serif", Georgia, serif; font-weight: 400;
    color: var(--brand); font-size: 41px; line-height: 1; margin-bottom: 20px;
  }
  .about-copy p { margin-bottom: 12px; }

  /* Services */
  .services { top: 1138px; height: 466px; background: var(--band); }
  .services .section-title { top: 42px; }
  .service-card {
    top: 113px; width: 498px; height: 281px; background: var(--paper);
    border-radius: 10px; box-shadow: 0 2px 8px rgba(0,0,0,.08);
    text-align: center; padding: 48px 38px 0;
  }
  .service-card h3 {
    font-family: "Bree Serif", Georgia, serif; font-weight: 400;
    color: var(--brand); font-size: 29px; line-height: 1; margin-bottom: 14px;
  }
  .service-card p { font-size: 14.5px; line-height: 25px; }
  .read-more {
    display: inline-block; margin-top: 10px;
    font-family: "Bree Serif", Georgia, serif; font-size: 17px;
    color: var(--brand); text-decoration: underline; text-underline-offset: 3px;
  }

  /* Testimonials */
  .testimonials { top: 1604px; height: 431px; }
  .testimonials .section-title { top: 46px; }
  .client-avatar {
    left: 554px; top: 135px; width: 88px; height: 88px; border-radius: 14px;
    border: 3px solid var(--paper); box-shadow: 0 1px 6px rgba(0,0,0,.25);
    background: linear-gradient(160deg, #d8c2b5, #a97e6d 60%, #7e5b52);
  }
  .quote {
    left: 160px; top: 246px; width: 880px; text-align: center;
    font-style: italic; font-size: 15px; line-height: 25px; color: var(--body);
  }
  .client-name { left: 0; top: 310px; width: 1200px; text-align: center; font-size: 15px; color: var(--muted); }
  .slider-dots { left: 542px; top: 359px; display: flex; gap: 9px; }
  .slider-dots span { width: 30px; height: 3px; background: #d0d0d0; }
  .slider-dots span.on { background: var(--brand); }

  /* Blog */
  .blog { top: 2035px; height: 664px; background: var(--band); }
  .blog .section-title { top: 46px; }
  .post { background: var(--paper); box-shadow: 0 2px 6px rgba(0,0,0,.1); overflow: hidden; }
  .post-photo { position: absolute; }
  .post-body { position: absolute; }
  .post-date { display: flex; align-items: center; gap: 10px; font-size: 14px; color: var(--ink); margin-bottom: 10px; }
  .post-title {
    font-family: "Bree Serif", Georgia, serif; font-weight: 400;
    font-size: 17.5px; line-height: 28px; color: var(--ink); margin-bottom: 8px;
  }
  .post-body p { font-size: 14px; line-height: 25px; }

  /* Footer */
  .site-footer { top: 2699px; height: 378px; background: var(--footer); color: var(--footer-text); }
  .footer-nav { left: 78px; top: 32px; display: flex; gap: 34px; font-size: 15px; }
  .footer-nav a { color: var(--footer-text); text-decoration: none; }
  .social { left: 906px; top: 22px; display: flex; gap: 10px; }
  .social span { width: 46px; height: 46px; border: 1.5px solid #cfcfcf; border-radius: 50%; }
  .footer-rule { left: 0; top: 86px; width: 1200px; height: 1px; background: var(--footer-line); }
  .newsletter-note { left: 78px; top: 152px; font-size: 15px; }
  .newsletter-form { left: 78px; top: 199px; display: flex; }
  .email-field {
    width: 342px; height: 44px; border: 1px solid #9a9a9a; background: transparent;
    color: #aaa; font-style: italic; font-size: 14px; padding: 12px 16px;
  }
  .send-button { width: 72px; height: 44px; background: var(--paper); display: flex; align-items: center; justify-content: center; }
  .footer-logo {
    right: 82px; top: 182px; font-family: "Raleway", "Asap", sans-serif; font-weight: 700;
    font-size: 54px; line-height: 1; color: var(--brand);
  }
  .legal {
    left: 0; top: 316px; width: 1200px; height: 62px; background: var(--footer-deep);
    border-top: 1px solid var(--footer-line);
    text-align: center; font-size: 14.5px; line-height: 60px;
  }
</style>
</head>
<body>

<header class="hero">
  <div class="hero-art" role="img" aria-label="Soft blue background photo of a hand touching a digital security interface with padlock and technology icons"></div>
  <nav class="main-nav">
    <a class="active" href="#">Home</a>
    <a href="#">About</a>
    <a href="#">Services</a>
    <a href="#">Contact</a>
  </nav>
  <h1 class="hero-title">zorvan lumet</h1>
</header>

<section class="about">
  <div class="abs about-frame">
    <div class="abs about-photo" role="img" aria-label="Photo of colleagues working together at a computer in a bright office"></div>
  </div>
  <div class="abs about-copy">
    <h2>About zorvan lumet</h2>
    <p>Lorem Ipsum is simply dummy text of the printing and typesetting industry. Lorem Ipsum has been the industry's standard dummy text ever since the 1500s, when an unknown printer took a galley.</p>
    <p>It has survived not only five centuries, but also the leap into electronic typesetting, remaining essentially unchanged.</p>
  </div>
</section>

<section class="services">
  <h2 class="section-title">Our Services</h2>
  <article class="abs service-card" style="left:78px">
    <h3>IT security</h3>
    <p>Lorem Ipsum is simply dummy text of the printing and typesetting industry. Lorem Ipsum has been the industry's standard dummy text ever since the 1500s, when an unknown printer took a galley of type and scrambled it to make a type specimen book.</p>
    <a class="read-more" href="#">READ MORE</a>
  </article>
  <article class="abs service-card" style="left:623px">
    <h3>IT support</h3>
    <p>Lorem Ipsum is simply dummy text of the printing and typesetting industry. Lorem Ipsum has been the industry's standard dummy text ever since the 1500s, when an unknown printer took a galley of type and scrambled it to make a type specimen book.</p>
    <a class="read-more" href="#">READ MORE</a>
  </article>
</section>

<section class="testimonials">
  <h2 class="section-title">Testimonials</h2>
  <div class="abs client-avatar" role="img" aria-label="Client portrait photo"></div>
  <p class="abs quote">Lorem Ipsum is simply dummy text of the printing and typesetting industry. Lorem Ipsum has been the industry's standard dummy text ever since the 1500s, when an unknown printer took a galley of type and scrambled it to make.</p>
  <div class="abs client-name">– Client Name</div>
  <div class="abs slider-dots"><span class="on"></span><span></span><span></span></div>
</section>

<section class="blog">
  <h2 class="section-title">Latest Blog</h2>

  <article class="abs post" style="left:78px; top:110px; width:332px; height:476px;">
    <div class="post-photo" style="left:0; top:0; width:332px; height:228px; background:linear-gradient(135deg,#5b7f99 0%,#a9bccb 45%,#e6ecf0 70%,#b38f6c 100%);" role="img" aria-label="Photo of hands typing on a laptop"></div>
    <div class="post-body" style="left:18px; top:254px; width:296px;">
      <div class="post-date"><svg width="16" height="16" viewBox="0 0 16 16" fill="none" stroke="#777" stroke-width="1.2"><rect x="1.5" y="2.5" width="13" height="12"/><line x1="1.5" y1="6" x2="14.5" y2="6"/><line x1="5" y1="1" x2="5" y2="4"/><line x1="11" y1="1" x2="11" y2="4"/></svg>29 May 2017</div>
      <h3 class="post-title">Lorem Ipsum is simply dummy text of the printing and typesetting.</h3>
      <p>Lorem Ipsum is simply dummy text of the printing and typesetting industry. Lorem Ipsum has been the industry's standard.</p>
    </div>
  </article>

  <article class="abs post" style="left:435px; top:110px; width:685px; height:228px;">
    <div class="post-photo" style="left:0; top:0; width:340px; height:228px; background:linear-gradient(120deg,#cfd8de 0%,#f2f4f5 40%,#8e9aa3 75%,#dfe4e7 100%);" role="img" aria-label="Photo of two colleagues reviewing work at a desk"></div>
    <div class="post-body" style="left:370px; top:30px; width:300px;">
      <div class="post-date"><svg width="16" height="16" viewBox="0 0 16 16" fill="none" stroke="#777" stroke-width="1.2"><rect x="1.5" y="2.5" width="13" height="12"/><line x1="1.5" y1="6" x2="14.5" y2="6"/><line x1="5" y1="1" x2="5" y2="4"/><line x1="11" y1="1" x2="11" y2="4"/></svg>29 May 2017</div>
      <h3 class="post-title">Lorem Ipsum is simply dummy text of the printing and typesetting.</h3>
      <p>Lorem Ipsum is simply dummy text of the printing and typesetting industry. Lorem Ipsum has been the industry's standard.</p>
    </div>
  </article>

  <article class="abs post" style="left:435px; top:363px; width:685px; height:227px;">
    <div class="post-body" style="left:26px; top:30px; width:300px;">
      <div class="post-date"><svg width="16" height="16" viewBox="0 0 16 16" fill="none" stroke="#777" stroke-width="1.2"><rect x="1.5" y="2.5" width="13" height="12"/><line x1="1.5" y1="6" x2="14.5" y2="6"/><line x1="5" y1="1" x2="5" y2="4"/><line x1="11" y1="1" x2="11" y2="4"/></svg>29 May 2017</div>
      <h3 class="post-title">Lorem Ipsum is simply dummy text of the printing and typesetting.</h3>
      <p>Lorem Ipsum is simply dummy text of the printing and typesetting industry. Lorem Ipsum has been the industry's standard.</p>
    </div>
    <div class="post-photo" style="left:346px; top:0; width:339px; height:227px; background:linear-gradient(120deg,#e8ecee 0%,#c5cdd2 40%,#6f7d87 70%,#d8dde0 100%);" role="img" aria-label="Photo of a support technician with a headset at a computer"></div>
  </article>
</section>

<footer class="site-footer">
  <nav class="abs footer-nav">
    <a href="#">Home</a><a href="#">About</a><a href="#">Services</a><a href="#">Contact</a>
  </nav>
  <div class="abs social" aria-label="Social links"><span></span><span></span><span></span><span></span></div>
  <div class="abs footer-rule"></div>
  <div class="abs newsletter-note">Get valuable content every day. Subscribe to our newsletter.</div>
  <div class="abs newsletter-form">
    <div class="email-field">Enter Your Email</div>
    <div class="send-button"><svg width="26" height="18" viewBox="0 0 26 18" fill="none" stroke="#26a6cf" stroke-width="1.6"><rect x="1" y="1" width="24" height="16"/><polyline points="1,1 13,10 25,1"/><line x1="1" y1="17" x2="10" y2="8"/><line x1="25" y1="17" x2="16" y2="8"/></svg></div>
  </div>
  <div class="abs footer-logo">zorvan lumet</div>
  <div class="abs legal">2018 ©zorvanlumet- All Rights Reserved.</div>
</footer>

</body>
</html>
```